Wordpress Design for a Private Label BBQ Brand

For our new brand, we'd need a new Wordpress website. We'd prefer to run the website on Wordpress

We'd like to include the following
- space for description of the brand
- space for product portfolio (not a shop!)
- space for socials
- space for support
- space for contact

```html
<!DOCTYPE html>
<html lang="en">
<head>
<meta charset="utf-8">
<title>Braciere – BBQ</title>
<link href="https://fonts.googleapis.com/css2?family=Montserrat:wght@400;500;600;700;800&display=swap" rel="stylesheet">
<style>
:root{
  --ink:#111;
  --black:#050505;
  --orange:#e5581f;
  --red:#b30f1f;
  --grey-band:#e8e9eb;
  --text:#333;
  --white:#fff;
}
*{margin:0;padding:0;box-sizing:border-box}
html,body{width:1200px;height:4539px;overflow:hidden}
body{position:relative;font-family:'Montserrat',sans-serif;color:var(--text);background:var(--white)}
.btn{position:absolute;display:flex;align-items:center;justify-content:center;background:var(--orange);color:var(--white);border:2px solid var(--red);border-radius:30px;font-weight:500}

/* hero */
.hero{position:absolute;left:0;top:0;width:1200px;height:573px;background:radial-gradient(ellipse at 30% 60%,#2a1a12 0%,var(--black) 60%)}
.hero-edge{position:absolute;left:0;top:520px;width:1200px;height:53px;background:linear-gradient(180deg,rgba(255,255,255,0),#fff)}
.brand{position:absolute;left:99px;top:18px;font-size:36px;font-weight:700;color:var(--white);letter-spacing:1px}
.nav{position:absolute;top:25px;left:470px;display:flex;gap:40px;font-size:16px;color:var(--white);font-weight:500}
.hero-title{position:absolute;left:97px;top:168px;font-size:88px;font-weight:800;color:var(--orange);line-height:1}
.hero-text{position:absolute;left:99px;top:283px;width:370px;font-size:13.5px;line-height:25px;color:var(--white)}
.hero-art{position:absolute;left:598px;top:88px;width:577px;height:460px;border-radius:45% 45% 30% 30%;border:3px solid var(--red);background:radial-gradient(ellipse at 50% 70%,#e0622a 0%,#5a2a1a 35%,#1a1a1a 70%)}

/* about */
.about-photo{position:absolute;left:113px;top:634px;width:447px;height:504px;border-radius:6px 6px 180px 6px;background:linear-gradient(135deg,#6b2a17,#c2461e 45%,#3b2620)}
h2{position:absolute;font-size:38px;font-weight:700;color:var(--ink);letter-spacing:.5px}
.about-text{position:absolute;left:620px;top:752px;width:487px;font-size:15px;line-height:24.8px}

/* portfolio */
.portfolio{position:absolute;left:0;top:1281px;width:1200px;height:828px;background:var(--grey-band)}
.product{position:absolute;background:radial-gradient(ellipse at center,#cfcfcf 0%,#f4f4f4 45%,#fff 70%)}
.product.lead{box-shadow:0 2px 10px rgba(0,0,0,.25)}

/* testimonial */
.testi-text{position:absolute;left:100px;top:2355px;width:423px;text-align:right;font-size:15px;line-height:24.8px}
.arrows{position:absolute;left:377px;top:2509px;width:145px;height:53px;background:var(--orange);border:2px solid var(--red);border-radius:30px}
.testi-photo{position:absolute;left:617px;top:2209px;width:449px;height:439px;border-radius:6px 6px 6px 180px;background:linear-gradient(160deg,#6b8a4a,#2d3a2a 55%,#5a3320)}

/* review */
.review{position:absolute;left:0;top:2791px;width:1200px;height:553px;background:linear-gradient(180deg,#dd4e1c,#b40f20)}
.card{position:absolute;top:2955px;width:487px;height:306px;background:var(--white);border-radius:4px}
.avatar{position:absolute;left:18px;top:23px;width:81px;height:81px;border-radius:50%;background:linear-gradient(160deg,#c9c9c9,#8a8a8a)}
.card-name{position:absolute;left:129px;top:50px;font-size:25px;font-weight:600;color:var(--ink)}
.card-text{position:absolute;left:28px;top:125px;width:450px;font-size:14px;line-height:25px}
.socials{position:absolute;left:32px;top:252px;display:flex;gap:18px;align-items:center}
.socials span{width:14px;height:14px;border-radius:50%;background:var(--ink)}
.socials span.ring{width:34px;height:34px;background:none;border:2px solid var(--ink)}

/* contact */
.field{position:absolute;height:56px;border-radius:28px;background:var(--white);box-shadow:0 0 0 2px #eee,0 3px 6px rgba(0,0,0,.12);font-size:14px;color:#444;padding:18px 20px}
.field.area{height:157px;border-radius:22px}

/* footer */
.footer{position:absolute;left:0;top:4053px;width:1200px;height:486px;background:linear-gradient(180deg,#fff 0,#1a1a1a 45px,var(--black) 70px)}
.foot-brand{position:absolute;left:118px;top:4326px;font-size:46px;font-weight:700;color:var(--white);letter-spacing:1px}
.foot-social{position:absolute;width:35px;height:35px;border-radius:50%;border:2px solid var(--red);top:4393px}
.foot-col{position:absolute;top:4196px;color:var(--white)}
.foot-col h3{font-size:19px;font-weight:700;margin-bottom:19px}
.foot-col li{list-style:none;font-size:14.5px;line-height:32.6px}
.contact-line{display:flex;gap:12px;font-size:14.5px;line-height:28px;margin-bottom:12px}
.contact-line svg{flex:none;margin-top:7px}
.rule{position:absolute;left:111px;top:4470px;width:978px;height:1px;background:#555}
.copy{position:absolute;top:4487px;left:0;width:1200px;text-align:center;font-size:14px;color:var(--white)}
</style>
</head>
<body>

<section class="hero">
  <div class="brand">BRACIERE</div>
  <nav class="nav"><span>Home</span><span>About Us</span><span>Product Portfolio</span><span>Support</span><span>Socials</span><span>Contact</span></nav>
  <h1 class="hero-title">Braciere</h1>
  <p class="hero-text">Lorem ipsum dolor sit amet, consectetur adipiscing elit, sed do eiusmod tempor incididunt ut labore et dolore magna aliqua.</p>
  <div class="btn" style="left:99px;top:391px;width:179px;height:46px;font-size:18px">Get Started</div>
  <div class="hero-art" role="img" aria-label="Charcoal kettle grill with flames inside a flame-shaped frame"></div>
  <div class="hero-edge"></div>
</section>

<section class="about">
  <div class="about-photo" role="img" aria-label="Steaks searing on a hot grill"></div>
  <h2 style="left:620px;top:678px">ABOUT US</h2>
  <p class="about-text">Lorem ipsum dolor sit amet, consectetur adipiscing elit, sed do eiusmod tempor incididunt ut labore et dolore magna aliqua. Ut enim ad minim veniam, quis nostrud exercitation ullamco laboris nisi ut aliquip ex ea commodo consequat. Duis aute irure dolor in reprehenderit in voluptate velit esse cillum dolore eu fugiat nulla pariatur.Lorem ipsum dolor sit amet, consectetur adipiscing elit, sed do eiusmod tempor incididunt ut labore et dolore magna aliqua. Ut enim ad minim veniam, quis nostrud exercitation ullamco laboris nisi ut aliquip ex ea commodo consequat. Duis aute irure dolor in reprehenderit in voluptate velit esse cillum dolore eu fugiat nulla pariatur.</p>
  <div class="btn" style="left:618px;top:1062px;width:180px;height:51px;font-size:18px">Read More</div>
</section>

<section class="portfolio"></section>
<h2 style="left:0;width:1200px;text-align:center;top:1366px">PRODUCT PORTFOLIO</h2>
<div class="product lead" style="left:76px;top:1455px;width:488px;height:242px" role="img" aria-label="Ceramic kamado grill, side view"></div>
<div class="product" style="left:587px;top:1455px;width:262px;height:242px" role="img" aria-label="Kamado grill with lid open"></div>
<div class="product" style="left:869px;top:1455px;width:262px;height:242px" role="img" aria-label="Compact kamado grill on stand"></div>
<div class="product" style="left:72px;top:1721px;width:263px;height:242px" role="img" aria-label="Grill tool detail"></div>
<div class="product" style="left:354px;top:1721px;width:263px;height:242px" role="img" aria-label="BBQ tong, fork and spatula set"></div>
<div class="product" style="left:640px;top:1721px;width:488px;height:242px" role="img" aria-label="Kamado grill with hinged lid"></div>
<div class="btn" style="left:470px;top:2009px;width:258px;height:49px;font-size:21px">View All Product</div>

<section class="testimonial">
  <h2 style="left:100px;width:434px;text-align:right;top:2290px">TESTIMONIAL</h2>
  <p class="testi-text">Lorem ipsum dolor sit amet, consectetur adipiscing elit, sed do eiusmod tempor incididunt ut labore et dolore magna aliqua. Ut enim ad minim veniam, quis nostrud exercitation ullamco laboris nisi ut aliquip ex ea commodo consequat.</p>
  <div class="arrows">
    <svg width="145" height="53" viewBox="0 0 145 53"><g stroke="#fff" stroke-width="3" fill="none" stroke-linecap="round"><path d="M20 26h36M28 19l-8 7 8 7"/><path d="M87 26h38M117 19l8 7-8 7"/></g></svg>
  </div>
  <div class="testi-photo" role="img" aria-label="Meat being turned with tongs on a kettle grill at an outdoor gathering"></div>
</section>

<section class="review"></section>
<h2 style="left:0;width:1200px;text-align:center;top:2868px;color:var(--white)">REVIEW</h2>
<article class="card" style="left:100px">
  <div class="avatar" role="img" aria-label="Reviewer portrait"></div>
  <div class="card-name">LOREM IPSUM</div>
  <p class="card-text">Sed ut perspiciatis unde omnis iste natus error sit voluptatem accusantium doloremque laudantium, totam rem aperiam, eaque ipsa quae ab illo inventore veritatis et quasi architecto beatae vitae dicta sunt explicabo.</p>
  <div class="socials"><span></span><span></span><span></span><span class="ring"></span></div>
</article>
<article class="card" style="left:617px">
  <div class="avatar" role="img" aria-label="Reviewer portrait"></div>
  <div class="card-name">LOREM IPSUM</div>
  <p class="card-text">Sed ut perspiciatis unde omnis iste natus error sit voluptatem accusantium doloremque laudantium, totam rem aperiam, eaque ipsa quae ab illo inventore veritatis et quasi architecto beatae vitae dicta sunt explicabo.</p>
  <div class="socials"><span></span><span></span><span></span><span class="ring"></span></div>
</article>

<section class="contact">
  <h2 style="left:0;width:1226px;text-align:center;top:3472px">CONTACT US</h2>
  <div class="field" style="left:111px;top:3554px;width:470px">First Name</div>
  <div class="field" style="left:604px;top:3554px;width:473px">Last Name</div>
  <div class="field" style="left:111px;top:3632px;width:470px">Phone</div>
  <div class="field" style="left:604px;top:3632px;width:473px">Email Address</div>
  <div class="field area" style="left:111px;top:3713px;width:960px">Message</div>
  <div class="btn" style="left:525px;top:3920px;width:152px;height:45px;font-size:16px">Submit Now</div>
</section>

<footer class="footer"></footer>
<div class="foot-brand">BRACIERE</div>
<div class="foot-social" style="left:117px"></div>
<div class="foot-social" style="left:185px"></div>
<div class="foot-social" style="left:252px"></div>
<div class="foot-social" style="left:319px"></div>
<div class="foot-col" style="left:396px"><h3>USE LINK</h3><ul><li>Home</li><li>About Us</li><li>Product Portfolio</li><li>Support</li><li>Socials</li><li>Contact</li></ul></div>
<div class="foot-col" style="left:633px"><h3>HELP LINKS</h3><ul><li>Terms &amp; Conditions</li><li>Privacy Policy</li><li>About Us</li><li>Support</li></ul></div>
<div class="foot-col" style="left:892px;width:220px">
  <h3>CONTACT</h3>
  <div class="contact-line"><svg width="12" height="14" viewBox="0 0 12 14"><path d="M6 0a5 5 0 0 0-5 5c0 4 5 9 5 9s5-5 5-9a5 5 0 0 0-5-5zm0 7a2 2 0 1 1 0-4 2 2 0 0 1 0 4z" fill="#fff"/></svg><span>4210 Lorem ipsum dolor sit amet, consectetur</span></div>
  <div class="contact-line"><svg width="12" height="12" viewBox="0 0 12 12"><path d="M2.5 0.5l2 2.5-1.2 1.5a7 7 0 0 0 4.2 4.2L9 7.5l2.5 2-1.5 2C5 11.5 0.5 7 0.5 2z" fill="#fff"/></svg><span>+1 555-010-2040</span></div>
  <div class="contact-line"><svg width="14" height="11" viewBox="0 0 14 11"><rect x="0.75" y="0.75" width="12.5" height="9.5" fill="none" stroke="#fff" stroke-width="1.5"/><path d="M1 1l6 5 6-5" fill="none" stroke="#fff" stroke-width="1.5"/></svg><span>info@braciere.example</span></div>
</div>
<div class="rule"></div>
<div class="copy">© Copyrights 2023 &nbsp; Braciere &nbsp;| &nbsp;All Rights Reserved</div>

</body>
</html>
```